FREE Network Assessment image for landing page

This graphic will be on a landing page and on the left will be Text and a download button that we change and control. The graphic for this project will be to the right.
I will add an example of the landing page area so that it makes more sense.

Please include the text from the sample - the font needs to be the same style as what we are using on the left side!

The graphic needs to be a .png file, roughly 713 x 527 white background. Use discretion on design layout.

Colors are black, Red = PMS 1795 and Gray = Cool Gray 10

Thanks,
Tom Garrick

Target Market(s)

small businesses

Industry/Entity Type

Information Technology

Font styles to use
Other font styles liked:
• See sample

Requirements
Must have
• see description
Nice to have
• Possibly small technology related image to help enhance the text but I don't want any image to compete with the text. Keep in mind the colors mentioned in the description - this is the web site colors.
Should not have
• Should not be hard to read

```html
<!DOCTYPE html>
<html lang="en">
<head>
<meta charset="utf-8">
<title>Free Network &amp; Computer Health Check</title>
<link rel="stylesheet" href="https://fonts.googleapis.com/css2?family=Oswald:wght@300;400;500&display=swap">
<style>
  :root {
    --backdrop: #9a9a9a;
    --paper: #fafafa;
    --brand-red: #de3131;
    --cool-gray: #63666a;
    --nav-active: #5f5d5c;
    --white: #ffffff;
  }
  * { margin: 0; padding: 0; box-sizing: border-box; }
  html, body {
    width: 1200px; height: 838px; overflow: hidden;
    background: var(--backdrop);
    font-family: "Oswald", "Arial Narrow", sans-serif;
  }
  .card {
    position: absolute; left: 244px; top: 166px;
    width: 712px; height: 506px;
    background: var(--paper);
  }
  .main-nav {
    position: absolute; left: 17px; top: 33px;
    width: 681px; height: 65px;
    background: var(--brand-red);
    border-radius: 4px 0 0 4px;
    box-shadow: 0 6px 10px rgba(0,0,0,0.18);
    overflow: hidden;
  }
  .nav-item {
    position: absolute; top: 0; height: 65px; line-height: 65px;
    color: var(--white); font-weight: 500; font-size: 19px;
    letter-spacing: 0.3px; white-space: nowrap;
  }
  .nav-item.is-active {
    background: var(--nav-active); text-align: center; width: 95px; left: 78px;
  }
  .nav-caret { display: inline-block; margin-left: 8px; vertical-align: middle; }
  .headline {
    position: absolute; left: 44px; top: 188px;
    font-weight: 400; font-size: 37px; line-height: 1;
    color: var(--cool-gray); letter-spacing: -0.2px; white-space: nowrap;
  }
  .checklist { position: absolute; left: 44px; top: 228px; list-style: none; }
  .checklist li {
    display: flex; align-items: center; height: 28px;
    font-weight: 300; font-size: 13.5px; color: var(--cool-gray);
    white-space: nowrap;
  }
  .checklist svg { width: 16px; height: 16px; margin-right: 8px; flex: none; }
  .cta-button {
    position: absolute; left: 44px; top: 414px;
    width: 215px; height: 43px; border-radius: 22px;
    background: var(--brand-red); color: var(--white);
    font-weight: 400; font-size: 14.5px; line-height: 43px; text-align: center;
    letter-spacing: -0.2px;
    box-shadow: 0 10px 14px -6px rgba(222,49,49,0.45);
  }
</style>
</head>
<body>
  <main class="card">
    <nav class="main-nav">
      <span class="nav-item is-active">HOME</span>
      <span class="nav-item" style="left:198px">ABOUT</span>
      <span class="nav-item" style="left:300px">TEAM</span>
      <span class="nav-item" style="left:374px">WHAT MAKES US DIFFERENT<svg class="nav-caret" width="9" height="6" viewBox="0 0 9 6"><path d="M1 1l3.5 3.5L8 1" fill="none" stroke="#fff" stroke-width="1.6"/></svg></span>
      <span class="nav-item" style="left:641px">SERVICES</span>
    </nav>

    <h1 class="headline">FREE Network &amp; Computer health check Service</h1>

    <ul class="checklist">
      <li><svg viewBox="0 0 16 16"><rect x="1" y="3" width="11" height="11" fill="none" stroke="#63666a" stroke-width="1.2"/><path d="M3.5 8l3 3.2L14.5 1" fill="none" stroke="#de3131" stroke-width="1.6"/></svg>Check your network’s security against hacker attacks, theft, ransomware, viruses, and more.</li>
      <li><svg viewBox="0 0 16 16"><rect x="1" y="3" width="11" height="11" fill="none" stroke="#63666a" stroke-width="1.2"/><path d="M3.5 8l3 3.2L14.5 1" fill="none" stroke="#de3131" stroke-width="1.6"/></svg>See who and what has access to your network and data.</li>
      <li><svg viewBox="0 0 16 16"><rect x="1" y="3" width="11" height="11" fill="none" stroke="#63666a" stroke-width="1.2"/><path d="M3.5 8l3 3.2L14.5 1" fill="none" stroke="#de3131" stroke-width="1.6"/></svg>Perform network and Internet speed test</li>
      <li><svg viewBox="0 0 16 16"><rect x="1" y="3" width="11" height="11" fill="none" stroke="#63666a" stroke-width="1.2"/><path d="M3.5 8l3 3.2L14.5 1" fill="none" stroke="#de3131" stroke-width="1.6"/></svg>Resolve PC slowness issues, security vulnerabilities and improper configurations</li>
      <li><svg viewBox="0 0 16 16"><rect x="1" y="3" width="11" height="11" fill="none" stroke="#63666a" stroke-width="1.2"/><path d="M3.5 8l3 3.2L14.5 1" fill="none" stroke="#de3131" stroke-width="1.6"/></svg>Validate your backups are working and recoverable in a timely fashion.</li>
    </ul>

    <div class="cta-button">BOOK AN APPOINTMENT NOW!</div>
  </main>
</body>
</html>
```